Valdane Companies Business Card Design

We need a new business card for our Private Equity Real Estate Development firm, “Valdane” and our EB-5 regional center “Thornmere Regional Center” on one card. We prefer a design that is simple, elegant, and represents the luxury products we design and build as well as the financial security and stability our successful history has produced. We are an industry leader in our field and 3rd generation family business that has evolved into an institutional quality investment platform. Considered design size is standard business card dimensions (3.5 x 2 inches with an additional 1/8 inch space for design elements or backgrounds that extend beyond the finished size of your piece.

Target Market(s)

• High net worth individuals
• Highly skilled technical workers and physicians in the US seeking investment-based immigration opportunities
• Sophisticated private equity investors
• Intermediary partners include domestic attorneys and investment brokers, as well as international agent networks
• US real estate developers

Industry/Entity Type

Finance

Contact Information for Business Card

(Providing placeholder info for personal information, please design for longer character spaces, longer names and addresses etc..)
• Logo for Valdane
• Logo for Thornmere Regional Center
• Full name: Marcus Valdane
• Job title: CEO
• Email address: mvaldane@valdanecompanies.com
• Cell phone number: +1.555.314.2287
• Office number +1.555.628.4410
• Office address: Larkfield Court 5, 4817 Vista Orilla, Brenton Hills, CA.
• Website: www.valdanecompanies.com

Font styles to use
Serif
Sans Serif

Colors
ec1f27
ffffff
000000

Requirements
Must have
• • Logo for Valdane
• • Logo for Thornmere Regional Center
• - Use rounded corners
• (See .ai file included for logos)
Nice to have
• • Simple, elegant design
• • Aesthetically compatible with our website design (www.valdanecompanies.com)
• • Color palette including but not limited to white, black, and red (as per logos)
Should not have
• - Not too much red color
• - Do not stack both logos on top of each other

```html
<!DOCTYPE html>
<html lang="en">
<head>
<meta charset="utf-8">
<title>Valdane Companies Business Card</title>
<link href="https://fonts.googleapis.com/css2?family=Cinzel:wght@700&family=Montserrat:wght@500&family=Tinos:wght@400;700&display=swap" rel="stylesheet">
<style>
  :root {
    --stage: #1b1b1f;
    --ink-navy: #12121e;
    --map-tone: #232333;
    --silver: #e6e6ea;
    --paper: #ffffff;
    --brand-red: #a8182f;
    --text-grey: #3a3a44;
    --rule-red: #c3324a;
  }
  * { margin: 0; padding: 0; box-sizing: border-box; }
  html, body { width: 1200px; height: 800px; overflow: hidden; background: var(--stage); }
  .canvas { position: relative; width: 1200px; height: 800px; }

  .card {
    position: absolute; top: 248px; width: 530px; height: 303px;
    border-radius: 18px; overflow: hidden;
  }

  /* Back side */
  .card-back { left: 45px; background: var(--ink-navy); }
  .world-map {
    position: absolute; left: 70px; top: 40px; width: 390px; height: 220px;
    border-radius: 40%;
    background: radial-gradient(ellipse at center, var(--map-tone) 0%, rgba(35,35,51,0.4) 55%, rgba(18,18,30,0) 75%);
  }
  .back-brand {
    position: absolute; left: 0; right: 0; top: 110px;
    display: flex; flex-direction: column; align-items: center;
  }
  .back-brand .wordmark {
    display: flex; align-items: center; gap: 14px;
    font-family: "Cinzel", serif; font-weight: 700; font-size: 40px;
    color: var(--silver); letter-spacing: 2px;
  }
  .back-brand .mark-square { width: 22px; height: 22px; background: var(--silver); }
  .back-brand .descriptor {
    margin-top: 6px; font-family: "Montserrat", sans-serif; font-weight: 500;
    font-size: 12px; letter-spacing: 9px; color: var(--silver); padding-left: 36px;
  }

  /* Front side */
  .card-front { left: 625px; background: var(--paper); }
  .card-front .base-band {
    position: absolute; left: 0; right: 0; bottom: 0; height: 12px; background: var(--brand-red);
  }
  .center-brand {
    position: absolute; left: 36px; top: 42px; display: flex; align-items: center; gap: 14px;
  }
  .center-brand .mark-square { width: 34px; height: 34px; background: var(--brand-red); }
  .center-brand .divider { width: 1px; height: 56px; background: var(--rule-red); }
  .center-brand .name {
    font-family: "Cinzel", serif; font-weight: 700; font-size: 34px; color: var(--brand-red); line-height: 1;
  }
  .center-brand .descriptor {
    margin-top: 6px; font-family: "Montserrat", sans-serif; font-weight: 500;
    font-size: 10px; letter-spacing: 7px; color: var(--brand-red);
  }

  .person { position: absolute; left: 36px; top: 160px; }
  .person .full-name { font-family: "Tinos", serif; font-weight: 700; font-size: 22px; color: var(--brand-red); line-height: 1.1; }
  .person .job-title { font-family: "Tinos", serif; font-size: 13px; color: var(--text-grey); }

  .contact-list {
    position: absolute; left: 36px; top: 214px; list-style: none;
    font-family: "Tinos", serif; font-size: 12.5px; color: var(--text-grey);
  }
  .contact-list li { display: flex; align-items: center; gap: 5px; height: 19px; white-space: nowrap; }
  .contact-list .sep { color: var(--brand-red); margin: 0 3px; }
  .contact-list svg { width: 11px; height: 11px; flex: none; }
  .contact-list .web { color: var(--brand-red); }
</style>
</head>
<body>
<div class="canvas">

  <section class="card card-back" aria-label="Card back">
    <div class="world-map" role="img" aria-label="Faint world map behind the brand name"></div>
    <div class="back-brand">
      <div class="wordmark"><span class="mark-square"></span>VALDANE</div>
      <div class="descriptor">CAPITAL</div>
    </div>
  </section>

  <section class="card card-front" aria-label="Card front">
    <div class="center-brand">
      <span class="mark-square"></span>
      <span class="divider"></span>
      <div>
        <div class="name">THORNMERE</div>
        <div class="descriptor">REGIONAL CENTER</div>
      </div>
    </div>

    <div class="person">
      <div class="full-name">Marcus Valdane</div>
      <div class="job-title">CEO</div>
    </div>

    <ul class="contact-list">
      <li>
        <svg viewBox="0 0 12 12"><rect x="3" y="0.8" width="6" height="10.4" rx="1" fill="none" stroke="#a8182f" stroke-width="1.2"/></svg>
        +1.555.314.2287<span class="sep">|</span>
        <svg viewBox="0 0 12 12"><path d="M1 4 Q6 0 11 4 L9.5 5.5 L8 4.5 L4 4.5 L2.5 5.5 Z M2.5 6 H9.5 V11 H2.5 Z" fill="#a8182f"/></svg>
        +1.555.628.4410<span class="sep">|</span>
        <svg viewBox="0 0 12 12"><rect x="0.5" y="2" width="11" height="8" fill="#a8182f"/><path d="M0.5 2 L6 6.5 L11.5 2" fill="none" stroke="#fff" stroke-width="1"/></svg>
        mvaldane@valdanecompanies.com
      </li>
      <li>
        <svg viewBox="0 0 12 12"><path d="M6 11.5 C6 11.5 1.8 6.8 1.8 4.4 A4.2 4.2 0 0 1 10.2 4.4 C10.2 6.8 6 11.5 6 11.5 Z" fill="none" stroke="#a8182f" stroke-width="1.3"/><circle cx="6" cy="4.4" r="1.4" fill="#a8182f"/></svg>
        Larkfield Court 5, 4817 Vista Orilla, Brenton Hills, CA.
      </li>
      <li>
        <svg viewBox="0 0 12 12"><circle cx="6" cy="6" r="5.5" fill="#a8182f"/><path d="M0.5 6 H11.5 M6 0.5 C3 3.5 3 8.5 6 11.5 M6 0.5 C9 3.5 9 8.5 6 11.5" fill="none" stroke="#fff" stroke-width="0.8"/></svg>
        <span class="web">www.valdanecompanies.com</span>
      </li>
    </ul>

    <div class="base-band"></div>
  </section>

</div>
</body>
</html>
```